Business Card for Coastal Tundrabridge Advisory

We need a business card for Coastal Tundrabridge Advisory. The company website address is provided below. The company logo is attached. We provide specialized permafrost services to the mining, transportation, and oil & gas industries. The card should be prepared for:
Matthias Korhonen, PhD.
Coastal Tundrabridge Advisory
PO Box 418259
Quillwater, Alaska 99642
Direct: +1-907-555-0143
Email: mkorhonen@tundrabridgeadvisory.example
Website: www.coastaltundrabridgeadvisory.example

```html
<!DOCTYPE html>
<html lang="en">
<head>
<meta charset="utf-8">
<title>Coastal Tundrabridge Advisory — Business Card</title>
<link rel="stylesheet" href="https://fonts.googleapis.com/css2?family=Arimo:wght@400;700&display=swap">
<style>
  :root {
    --backdrop: #d9d9db;
    --card-dark: #111a22;
    --card-light: #f7f7f7;
    --ink-light: #ffffff;
    --ink-soft: #e4e7ea;
    --ink-dark: #141c24;
    --ink-muted: #2a3038;
  }
  * { box-sizing: border-box; margin: 0; padding: 0; }
  html, body {
    width: 1200px;
    height: 800px;
    overflow: hidden;
    background: var(--backdrop);
    font-family: "Arimo", Arial, sans-serif;
  }
  .canvas {
    width: 1200px;
    height: 800px;
    display: flex;
    align-items: center;
    justify-content: center;
    gap: 40px;
  }
  .card {
    position: relative;
    width: 520px;
    height: 298px;
    border-radius: 18px;
    overflow: hidden;
    box-shadow: 0 10px 26px rgba(0, 0, 0, 0.18);
  }

  /* Front: personal details */
  .card-front {
    background: var(--card-dark);
    color: var(--ink-light);
  }
  .front-wordmark {
    position: absolute;
    left: 30px;
    top: 150px;
    width: 190px;
    font-weight: 700;
    font-size: 19px;
    line-height: 1.15;
    color: var(--ink-light);
  }
  .contact-block {
    position: absolute;
    right: 28px;
    top: 26px;
    text-align: right;
  }
  .person-name {
    font-weight: 700;
    font-size: 22px;
    letter-spacing: 0.2px;
  }
  .person-title {
    font-size: 13px;
    color: var(--ink-soft);
    margin-top: 3px;
  }
  .address {
    font-size: 13px;
    line-height: 1.35;
    color: var(--ink-soft);
    margin-top: 22px;
  }
  .phone {
    font-size: 13px;
    color: var(--ink-soft);
    margin-top: 12px;
  }
  .email {
    font-size: 13px;
    color: var(--ink-soft);
    margin-top: 14px;
  }
  .web-bar {
    position: absolute;
    right: 0;
    bottom: 24px;
    width: 300px;
    height: 30px;
    background: var(--card-light);
    border-radius: 8px 0 0 8px;
    display: flex;
    align-items: center;
    justify-content: flex-end;
    padding-right: 20px;
    font-size: 12.5px;
    color: var(--ink-dark);
  }

  /* Back: brand side */
  .card-back {
    background: var(--card-light);
    color: var(--ink-dark);
    display: flex;
    flex-direction: column;
    align-items: center;
    justify-content: center;
  }
  .back-wordmark {
    font-weight: 700;
    font-size: 32px;
    line-height: 1.1;
    text-align: center;
    width: 420px;
    color: var(--ink-dark);
    margin-top: -10px;
  }
  .back-web {
    margin-top: 48px;
    font-size: 14px;
    color: var(--ink-muted);
  }
</style>
</head>
<body>
  <main class="canvas">
    <section class="card card-front" aria-label="Business card front">
      <div class="front-wordmark">Coastal Tundrabridge Advisory</div>
      <div class="contact-block">
        <p class="person-name">Matthias Korhonen, PhD.</p>
        <p class="person-title">President</p>
        <p class="address">PO Box 418259<br>Quillwater, Alaska 99642</p>
        <p class="phone">+1-907-555-0143</p>
        <p class="email">mkorhonen@tundrabridgeadvisory.example</p>
      </div>
      <div class="web-bar">www.coastaltundrabridgeadvisory.example</div>
    </section>

    <section class="card card-back" aria-label="Business card back">
      <div class="back-wordmark">Coastal Tundrabridge Advisory</div>
      <p class="back-web">www.coastaltundrabridgeadvisory.example</p>
    </section>
  </main>
</body>
</html>
```